Vorn upkeep KT Solar Venture

Solar power system install
Services and maintenance
wiring, Rewinding and Renovation
Switch Board Upgrade
Power and lighting point
t doesn’t matter how much you spend on quality parts, your solar system will let you down if your design and installation are sub-par. Have your solar system tailored and installed by our Master Electrician and Bright Grid Guild Accredited team.

Target Market(s)

sales and installed

Industry/Entity Type

Solar install and retailer

Contact Information for Business Card

Name , Email, Phone Number ,Business address,

Font styles to use
Serif

Colors
0054AA
0677BA
7BADD7
CADEEF
E8F1F8

Requirements
Must have
• clear and bright
Nice to have
• new design
Should not have
• unclear pictures

```html
<!DOCTYPE html>
<html lang="en">
<head>
<meta charset="utf-8">
<title>Vorn Upkeep – Business Card</title>
<link href="https://fonts.googleapis.com/css2?family=Roboto:wght@400;500;700;900&display=swap" rel="stylesheet">
<style>
  :root{
    --stage:#2d2d2d;
    --blue-deep:#0054AA;
    --blue-mid:#0677BA;
    --blue-light:#7BADD7;
    --blue-pale:#CADEEF;
    --blue-mist:#E8F1F8;
    --green:#2E9E3A;
    --green-lime:#7DBB2B;
    --white:#ffffff;
    --paper:#f1f1f0;
  }
  *{margin:0;padding:0;box-sizing:border-box}
  html,body{width:1200px;height:1138px;overflow:hidden;background:var(--stage);font-family:"Roboto",sans-serif}
  .card{position:absolute;width:620px;height:375px;border-radius:14px;overflow:hidden}
  .card-front{left:274px;top:185px}
  .card-back{left:276px;top:607px}
  .card svg.bg{position:absolute;inset:0;width:100%;height:100%}
  .brand{position:absolute;display:flex;align-items:center;gap:12px}
  .brand-dot{width:56px;height:56px;border-radius:50%;background:var(--blue-mist);flex:none}
  .brand-name{font-weight:900;text-transform:uppercase;line-height:1.05}
  .card-front .brand{right:30px;top:74px}
  .card-front .brand-name{color:var(--white);font-size:24px;letter-spacing:.3px}
  .services{position:absolute;right:30px;top:230px;list-style:none;text-align:right;color:var(--white);font-size:17px;line-height:22.3px}
  .services li::after{content:"«";margin-left:10px}
  .card-back .brand{left:28px;top:95px;flex-direction:column;gap:14px}
  .card-back .brand-dot{width:104px;height:104px;background:var(--blue-pale)}
  .card-back .brand-name{color:var(--blue-deep);font-size:28px;text-align:center;letter-spacing:.3px}
  .person{position:absolute;left:345px;top:58px;color:var(--white)}
  .person-name{color:var(--green-lime);font-size:26px;font-weight:500}
  .person-title{font-size:16px;margin-top:4px}
  .address{position:absolute;left:345px;top:170px;color:var(--white);font-size:16.5px;line-height:23.5px}
  .contacts{position:absolute;left:345px;top:233px;list-style:none;color:var(--white);font-size:16.5px;line-height:23.5px}
  .contacts li{display:flex;align-items:center;gap:18px}
  .contacts svg{width:14px;height:14px;flex:none}
  .tagline{position:absolute;left:345px;top:322px;color:var(--white);font-size:16.5px}
</style>
</head>
<body>

<section class="card card-front">
  <svg class="bg" viewBox="0 0 620 375" preserveAspectRatio="none">
    <defs>
      <linearGradient id="frontBlue" x1="0" y1="0" x2="0.3" y2="1">
        <stop offset="0" stop-color="#0054AA"/>
        <stop offset="1" stop-color="#0A86CF"/>
      </linearGradient>
      <linearGradient id="panelTone" x1="1" y1="0" x2="0" y2="1">
        <stop offset="0" stop-color="#c79a7c"/>
        <stop offset="0.35" stop-color="#5d6678"/>
        <stop offset="1" stop-color="#2a3142"/>
      </linearGradient>
    </defs>
    <rect width="620" height="375" fill="url(#frontBlue)"/>
    <path d="M0 0 H212 C275 90 300 230 205 375 H0 Z" fill="var(--green)"/>
    <path d="M0 0 H205 C263 90 285 230 198 375 H0 Z" fill="url(#panelTone)" role="img" aria-label="Photo of rooftop solar panels in warm sunlight"/>
  </svg>
  <div class="brand">
    <span class="brand-dot"></span>
    <span class="brand-name">Vorn Upkeep<br>Solar Venture</span>
  </div>
  <ul class="services">
    <li>Solar Power System Install</li>
    <li>Services &amp; Maintenance</li>
    <li>Switch Board Upgrade</li>
    <li>Power &amp; Lighting Point</li>
    <li>Wiring, Rewinding &amp; Renovation</li>
  </ul>
</section>

<section class="card card-back">
  <svg class="bg" viewBox="0 0 620 375" preserveAspectRatio="none">
    <defs>
      <linearGradient id="backBlue" x1="0" y1="0" x2="0.3" y2="1">
        <stop offset="0" stop-color="#0054AA"/>
        <stop offset="1" stop-color="#0A86CF"/>
      </linearGradient>
      <linearGradient id="stripGreen" x1="0" y1="0" x2="1" y2="0">
        <stop offset="0" stop-color="#1E9A3C"/>
        <stop offset="1" stop-color="#7DBB2B"/>
      </linearGradient>
    </defs>
    <rect width="620" height="375" fill="url(#backBlue)"/>
    <rect x="280" y="319" width="340" height="39" fill="url(#stripGreen)"/>
    <path d="M0 0 H250 C330 100 345 250 245 375 H0 Z" fill="var(--green)"/>
    <path d="M0 0 H242 C318 100 330 250 236 375 H0 Z" fill="var(--paper)"/>
  </svg>
  <div class="brand">
    <span class="brand-dot"></span>
    <span class="brand-name">Vorn Upkeep<br>Solar Venture</span>
  </div>
  <div class="person">
    <h1 class="person-name">Mara Lind Hollis</h1>
    <p class="person-title">Managing Director</p>
  </div>
  <p class="address">58 Meadow Row, Fernvale,<br>Brookton, US 204518</p>
  <ul class="contacts">
    <li><svg viewBox="0 0 14 14"><path d="M2 5 C2 2 12 2 12 5 L10 6 L9 4.5 H5 L4 6 Z M3 7 H11 V12 H3 Z" fill="var(--green-lime)"/></svg>555-204-7788</li>
    <li><svg viewBox="0 0 14 14"><rect x="1" y="3" width="12" height="8" fill="var(--green-lime)"/><path d="M1 3 L7 8 L13 3" stroke="var(--blue-deep)" stroke-width="1.2" fill="none"/></svg>mara@vornupkeep.com</li>
    <li><svg viewBox="0 0 14 14"><circle cx="7" cy="7" r="5.5" fill="none" stroke="var(--green-lime)" stroke-width="1.3"/><path d="M1.5 7 H12.5 M7 1.5 C4 4 4 10 7 12.5 C10 10 10 4 7 1.5" fill="none" stroke="var(--green-lime)" stroke-width="1"/></svg>www.vornupkeep.com</li>
  </ul>
  <p class="tagline">Solar power system install</p>
</section>

</body>
</html>
```